Redesign of business card for Cedar Ridge Mechanical

We are looking for a new design for our business cards for Cedar Ridge Mechanical. We are a plumbing & HVAC construction company, operating on the West Coast of Canada and USA. Logo attached.
Industry/Entity Type
Construction - Plumbing & HVAC
Contact Information for Business Card
Name, address, phone numbers, email, website address
Look and feel
Each slider illustrates characteristics of the customer's brand and the style your logo design should communicate.

```html
<!DOCTYPE html>
<html lang="en">
<head>
<meta charset="utf-8">
<title>Cedar Ridge Mechanical – Business Card</title>
<link rel="stylesheet" href="https://fonts.googleapis.com/css2?family=Montserrat:wght@400;500;700&display=swap">
<style>
  :root {
    --backdrop: #e6e2dc;
    --card-white: #ffffff;
    --card-black: #1c1c1c;
    --ink: #1e1e1e;
    --band-dark: #333333;
    --band-grey: #666666;
    --band-text: #ffffff;
    --emboss: #3c3c3c;
  }
  * { box-sizing: border-box; margin: 0; padding: 0; }
  html, body { width: 900px; height: 1200px; overflow: hidden; }
  body {
    position: relative;
    background: var(--backdrop);
    font-family: "Montserrat", sans-serif;
    color: var(--ink);
  }
  .card {
    position: absolute;
    left: 80px;
    width: 742px;
    height: 440px;
    border-radius: 22px;
    overflow: hidden;
  }
  .card--front { top: 131px; background: var(--card-white); }
  .card--back  { top: 638px; background: var(--card-black); }

  .brand-name {
    position: absolute;
    left: 118px;
    top: 168px;
    width: 220px;
    font-weight: 700;
    font-size: 26px;
    line-height: 1.2;
    text-transform: uppercase;
    color: var(--ink);
  }
  .divider {
    position: absolute;
    left: 356px;
    top: 156px;
    width: 2px;
    height: 146px;
    background: var(--ink);
  }
  .person { position: absolute; left: 374px; top: 152px; }
  .person__name { font-weight: 700; font-size: 25px; line-height: 30px; }
  .person__title { font-size: 15px; line-height: 22px; }

  .contacts {
    position: absolute;
    left: 374px;
    top: 223px;
    list-style: none;
  }
  .contacts li {
    display: flex;
    align-items: center;
    height: 30.5px;
    font-size: 15.5px;
  }
  .contacts svg { width: 16px; height: 16px; margin-right: 11px; fill: var(--ink); }

  .band {
    position: absolute;
    left: 0;
    top: 371px;
    width: 742px;
    height: 35px;
  }
  .address {
    position: absolute;
    left: 140px;
    top: 371px;
    width: 360px;
    line-height: 35px;
    text-align: center;
    font-size: 15.5px;
    color: var(--band-text);
  }

  .back-name {
    position: absolute;
    left: 0;
    top: 0;
    width: 742px;
    height: 440px;
    display: flex;
    align-items: center;
    justify-content: center;
    font-weight: 700;
    font-size: 40px;
    letter-spacing: 1px;
    text-transform: uppercase;
    color: var(--emboss);
  }
</style>
</head>
<body>

<section class="card card--front">
  <div class="brand-name">Cedar Ridge Mechanical</div>
  <div class="divider"></div>

  <div class="person">
    <div class="person__name">Daniel Brooks</div>
    <div class="person__title">Managing Director</div>
  </div>

  <ul class="contacts">
    <li>
      <svg viewBox="0 0 24 24" aria-hidden="true"><path d="M6.6 10.8a15 15 0 0 0 6.6 6.6l2.2-2.2a1 1 0 0 1 1-.25 11.4 11.4 0 0 0 3.6.57 1 1 0 0 1 1 1V20a1 1 0 0 1-1 1A17 17 0 0 1 3 4a1 1 0 0 1 1-1h3.5a1 1 0 0 1 1 1c0 1.25.2 2.45.57 3.6a1 1 0 0 1-.25 1z"/></svg>
      888.555.0142
    </li>
    <li>
      <svg viewBox="0 0 24 24" aria-hidden="true"><path d="M3 5h18v2l-9 6-9-6zM3 9l9 6 9-6v10H3z"/></svg>
      info@cedarridgemechanical.com
    </li>
    <li>
      <svg viewBox="0 0 24 24" aria-hidden="true"><path d="M12 2a10 10 0 1 0 0 20 10 10 0 0 0 0-20zm-1 17.9A8 8 0 0 1 4.1 11H7l2 3v2l2 2zm6.9-2.5A2 2 0 0 0 16 16h-1v-3a1 1 0 0 0-1-1H8v-2h2a1 1 0 0 0 1-1V7h2a2 2 0 0 0 2-2v-.4a8 8 0 0 1 2.9 12.8z"/></svg>
      www.cedarridgemechanical.com
    </li>
  </ul>

  <svg class="band" viewBox="0 0 742 35" aria-hidden="true">
    <polygon points="0,0 545,0 525,35 0,35" fill="var(--band-dark)"/>
    <polygon points="555,0 742,0 742,35 535,35" fill="var(--band-grey)"/>
  </svg>
  <div class="address">240 Harbor View Road Bellingham, WA 98225</div>
</section>

<section class="card card--back">
  <div class="back-name">Cedar Ridge Mechanical</div>
</section>

</body>
</html>
```